Indoor Air Restoration company needs graphic design for a 6x12 v nose trailer to wrap

We offer mold services, duct cleaning, water damage clean up and odor removal. "We find, fix and prevent mold, odor and allergen problems" is what we want to communicate on this trailer, which is a rolling billboard. We like the blue and orange color themes, as found in our logo. The company name is Brightwater Dwelling Services and the logo is attached below. We'd like to see our message clearly, company name and what we offer. We tend to lean towards white letters on a darker background (blue or orange) but are very open to outside ideas, as we are stuck! Our website is available for reference if that is helpful. www.brightwaterdwell.com The phone number to be printed on truck is 302-517-9046, Happy designing!!

Target Market(s)

Home owners

Industry/Entity Type

Indoor Air Quality, Mold Remediation

Font styles to use
Sans Serif

Colors
0054AA
0677BA
7BADD7
CADEEF
E8F1F8
F0912C
F2A743
F7CA91
FBE8D2
FDF5EE

Requirements
Must have
• our message, company name and phone
Nice to have
• services we offer (mold remediation, duct cleaning, water damage and odor removal
Should not have
• cartoon feel

```html
<!DOCTYPE html>
<html lang="en">
<head>
<meta charset="utf-8">
<title>Brightwater Dwelling Services – Trailer Wrap</title>
<link rel="stylesheet" href="https://fonts.googleapis.com/css2?family=Bebas+Neue&family=Poppins:wght@600&display=swap">
<style>
  :root {
    --ink: #0a101d;
    --panel: #0a0f1c;
    --bg-blue: #22409a;
    --bg-deep: #172c6e;
    --bg-plum: #6a2a55;
    --brand-blue: #1a78c8;
    --white: #ffffff;
    --water-a: #1d5fb0; --water-b: #24a2dc;
    --mold-a: #167a3a;  --mold-b: #6db048;
    --odor-a: #7a1518;  --odor-b: #d81e2c;
    --ducts-a: #e64e22; --ducts-b: #f5a33c;
    --phone-a: #e54b23; --phone-b: #f2a342;
    --web-a: #157a3a;   --web-b: #6cb048;
  }
  * { margin: 0; padding: 0; box-sizing: border-box; }
  html, body { width: 1200px; height: 600px; overflow: hidden; background: var(--ink); }
  .wrap { position: relative; width: 1200px; height: 600px; overflow: hidden; font-family: "Bebas Neue", sans-serif; }
  .backdrop { position: absolute; inset: 0; }
  .message-panel {
    position: absolute; left: 300px; top: 44px; width: 584px; height: 375px;
    background: var(--panel); border-radius: 22px;
  }
  .headline {
    position: absolute; left: 342px; top: 96px; width: 510px;
    color: var(--white); font-size: 50px; letter-spacing: 6.4px; line-height: 1; white-space: nowrap;
  }
  .services { position: absolute; left: 342px; top: 164px; display: flex; gap: 20px; }
  .service {
    width: 110px; height: 110px; border-radius: 16px; color: var(--white);
    display: flex; flex-direction: column; align-items: center; padding-top: 8px;
    font-size: 34px; line-height: 1;
  }
  .service-icon { width: 50px; height: 50px; margin-top: 10px; border-radius: 50%; background: rgba(255,255,255,0.22); }
  .service--water { background: linear-gradient(135deg, var(--water-a), var(--water-b)); }
  .service--mold  { background: linear-gradient(135deg, var(--mold-a), var(--mold-b)); }
  .service--odor  { background: linear-gradient(135deg, var(--odor-a), var(--odor-b)); }
  .service--ducts { background: linear-gradient(135deg, var(--ducts-a), var(--ducts-b)); }
  .contact { position: absolute; inset: 0; }
  .contact-text { font-family: "Poppins", sans-serif; font-weight: 600; fill: var(--white); }
  .phone-number { font-size: 47px; }
  .web-address { font-size: 28px; }
  .brand-name {
    position: absolute; color: var(--brand-blue); text-transform: uppercase; line-height: 0.95; text-align: center;
  }
  .brand-name--top { left: 38px; top: 78px; width: 170px; font-size: 38px; }
  .brand-name--side { left: 912px; top: 300px; width: 250px; font-size: 46px; }
</style>
</head>
<body>
<div class="wrap">
  <svg class="backdrop" width="1200" height="600" viewBox="0 0 1200 600" role="img" aria-label="Abstract background of overlapping diamonds with a soft dot texture in blue, plum and red tones">
    <defs>
      <linearGradient id="bgGrad" x1="0" y1="0" x2="1" y2="1">
        <stop offset="0" stop-color="var(--bg-blue)"/>
        <stop offset="0.55" stop-color="var(--bg-deep)"/>
        <stop offset="1" stop-color="var(--bg-plum)"/>
      </linearGradient>
    </defs>
    <rect width="1200" height="600" fill="url(#bgGrad)"/>
    <rect x="260" y="410" width="190" height="190" rx="22" transform="rotate(45 355 505)" fill="#8a2a4a" opacity="0.55"/>
    <rect x="420" y="460" width="150" height="150" rx="20" transform="rotate(45 495 535)" fill="#c0393f" opacity="0.55"/>
    <rect x="780" y="420" width="220" height="220" rx="24" transform="rotate(45 890 530)" fill="#9a3a5a" opacity="0.5"/>
    <rect x="860" y="-120" width="260" height="260" rx="28" transform="rotate(45 990 10)" fill="#8a3050" opacity="0.5"/>
    <rect x="-93" y="-25" width="306" height="306" rx="24" transform="rotate(45 60 128)" fill="var(--ink)"/>
  </svg>

  <div class="message-panel"></div>

  <h1 class="headline">WE FIND, FIX AND PREVENT</h1>

  <div class="services">
    <div class="service service--water">WATER<span class="service-icon" role="img" aria-label="Water drop icon"></span></div>
    <div class="service service--mold">MOLD<span class="service-icon" role="img" aria-label="Mold spore icon"></span></div>
    <div class="service service--odor">ODOR<span class="service-icon" role="img" aria-label="Odor wave icon"></span></div>
    <div class="service service--ducts">DUCTS<span class="service-icon" role="img" aria-label="Duct fan icon"></span></div>
  </div>

  <svg class="contact" width="1200" height="600" viewBox="0 0 1200 600">
    <defs>
      <linearGradient id="phoneBar" x1="0" x2="1"><stop offset="0" stop-color="var(--phone-a)"/><stop offset="1" stop-color="var(--phone-b)"/></linearGradient>
      <linearGradient id="webBar" x1="0" x2="1"><stop offset="0" stop-color="var(--web-a)"/><stop offset="1" stop-color="var(--web-b)"/></linearGradient>
    </defs>
    <path class="web-bar" d="M300 366 H890 V421 H318 A18 18 0 0 1 300 403 Z" fill="url(#webBar)"/>
    <path class="phone-bar" d="M269 289 H880 V366 H269 A20 20 0 0 1 249 346 V309 A20 20 0 0 1 269 289 Z" fill="url(#phoneBar)"/>
    <rect x="890" y="145" width="290" height="290" rx="34" transform="rotate(45 1035 290)" fill="var(--ink)"/>

    <g class="phone-icon">
      <circle cx="368" cy="328" r="18" fill="#eef2f7"/>
      <path d="M361 318 l4 -1 l3 6 l-3 2 q2 5 7 7 l2 -3 l6 3 l-1 4 q-2 2 -5 1 q-11 -4 -14 -14 q-1 -3 1 -5 z" fill="var(--phone-a)"/>
    </g>
    <text class="contact-text phone-number" x="414" y="346">302-517-9046</text>

    <g class="web-icon" fill="none" stroke="var(--white)" stroke-width="2.4">
      <circle cx="368" cy="393" r="17"/>
      <ellipse cx="368" cy="393" rx="7" ry="17"/>
      <line x1="351" y1="393" x2="385" y2="393"/>
    </g>
    <text class="contact-text web-address" x="414" y="403">brightwaterdwell.com</text>
  </svg>

  <div class="brand-name brand-name--top">Brightwater Dwelling Services</div>
  <div class="brand-name brand-name--side">Brightwater Dwelling Services</div>
</div>
</body>
</html>
```